New Company Business Card design

Looking for a corporate looking business card utilising my new logo design - the logo i would like embossed as one option and flat as another - simplistic but stylish - less is more - we are an import export business launching into the market - i would like a couple of options as main background - Grey or Black

```html
<!DOCTYPE html>
<html lang="en">
<head>
<meta charset="UTF-8">
<title>Northwind Trade Partners – Business Card</title>
<link rel="stylesheet" href="https://fonts.googleapis.com/css2?family=Open+Sans:wght@400;600;700&display=swap">
<style>
  :root {
    --brand-blue: #2f7bc6;
    --accent-silver: #a9abae;
    --card-grey: #3b3c3f;
    --card-black: #151516;
    --ink-light: #eeeeee;
    --rule: #6c6d70;
    --stage: #e4e4e4;
  }
  * { margin: 0; padding: 0; box-sizing: border-box; }
  html, body { width: 1200px; height: 900px; overflow: hidden; }
  body {
    background: var(--stage);
    font-family: "Open Sans", Arial, sans-serif;
    position: relative;
  }
  .card {
    position: absolute;
    width: 560px;
    height: 320px;
    border-radius: 22px;
    overflow: hidden;
    box-shadow: 0 12px 28px rgba(0,0,0,.28);
  }
  .card--front { left: 60px; top: 110px; background: var(--card-grey); }
  .card--back  { left: 580px; top: 470px; background: var(--card-black); }

  .front-band { position: absolute; inset: 0; width: 100%; height: 100%; }

  .holder {
    position: absolute;
    right: 34px; top: 22px;
    text-align: right;
    color: #ffffff;
  }
  .holder__name { font-weight: 700; font-size: 17px; letter-spacing: .3px; text-transform: uppercase; line-height: 22px; }
  .holder__role { font-weight: 400; font-size: 14px; line-height: 18px; }

  .brand {
    display: flex; align-items: center; gap: 10px;
    color: var(--brand-blue);
    font-weight: 700;
    text-transform: uppercase;
    letter-spacing: 1.5px;
    white-space: nowrap;
  }
  .brand__dot {
    width: 16px; height: 16px; border-radius: 50%;
    background: var(--brand-blue);
    flex: none;
  }
  .brand--front { position: absolute; left: 40px; top: 150px; font-size: 22px; }
  .brand--back { position: absolute; left: 0; right: 0; top: 144px; justify-content: center; font-size: 26px; }

  .contact {
    position: absolute;
    left: 40px; bottom: 28px;
    list-style: none;
    color: var(--ink-light);
    font-size: 14px;
    line-height: 21px;
  }
  .contact li { display: flex; align-items: center; gap: 8px; white-space: nowrap; }
  .contact svg { width: 13px; height: 13px; flex: none; }
  .icon-fill { fill: var(--brand-blue); }
  .icon-line { fill: none; stroke: var(--brand-blue); stroke-width: 2.4; stroke-linejoin: round; }

  .divider {
    position: absolute;
    left: 292px; bottom: 32px;
    width: 1px; height: 58px;
    background: var(--rule);
  }
  .address {
    position: absolute;
    left: 310px; bottom: 48px;
    font-size: 14px; line-height: 20px;
    color: var(--ink-light);
    font-style: normal;
    white-space: nowrap;
  }
</style>
</head>
<body>

<section class="card card--front" aria-label="Business card front">
  <svg class="front-band" viewBox="0 0 560 320" preserveAspectRatio="none" aria-hidden="true">
    <path d="M0 0 H560 V62 C420 66 200 80 40 130 C20 136 8 142 0 148 Z" fill="var(--brand-blue)"/>
    <path d="M0 156 C30 138 120 110 250 94 C360 80 470 72 560 70 V78 C470 80 360 88 250 102 C120 118 40 142 0 164 Z" fill="var(--accent-silver)"/>
  </svg>
  <div class="holder">
    <div class="holder__name">Dana Whitlock</div>
    <div class="holder__role">President</div>
  </div>
  <div class="brand brand--front"><span class="brand__dot"></span>Northwind Trade Partners</div>

  <ul class="contact">
    <li><svg viewBox="0 0 24 24"><path class="icon-fill" d="M6.6 10.8a15.1 15.1 0 006.6 6.6l2.2-2.2a1 1 0 011-.24 11.4 11.4 0 003.6.57 1 1 0 011 1V20a1 1 0 01-1 1A17 17 0 013 4a1 1 0 011-1h3.5a1 1 0 011 1c0 1.25.2 2.45.57 3.57a1 1 0 01-.25 1z"/></svg>(000) 555-01947</li>
    <li><svg viewBox="0 0 24 24"><rect class="icon-line" x="3" y="5" width="18" height="14" rx="1"/><path class="icon-line" d="M3 6l9 7 9-7"/></svg>hello@northwindtrade.com</li>
    <li><svg viewBox="0 0 24 24"><circle class="icon-line" cx="12" cy="12" r="9"/><path class="icon-line" d="M3 12h18M12 3c3 3 3 15 0 18M12 3c-3 3-3 15 0 18"/></svg>www.northwindtrade.com</li>
  </ul>
  <div class="divider"></div>
  <address class="address">P.O. Box 418, Harbor Lane,<br>Easton, Zip Code - 20410</address>
</section>

<section class="card card--back" aria-label="Business card back">
  <div class="brand brand--back"><span class="brand__dot"></span>Northwind Trade Partners</div>
</section>

</body>
</html>
```